Kelmo website design on shopify

Job Description:
As a web designer for Kelmo, you will be the driving force behind designing and developing our new e-commerce website. Your responsibility will be to create an attractive, functional, and intuitive online shopping experience where customers can effortlessly discover and purchase high-quality supplements such as pre-workout, creatine, and protein shakes. Your design will play a crucial role in enhancing our brand and engaging our target audience.

```html
<!DOCTYPE html>
<html lang="en">
<head>
<meta charset="utf-8">
<title>Kelmo — Fueling Health, Not Expenses</title>
<link href="https://fonts.googleapis.com/css2?family=Roboto:wght@400;500;700;900&display=swap" rel="stylesheet">
<style>
:root{
  --purple:#7b2185;
  --ink:#161616;
  --text:#2b2b2b;
  --white:#ffffff;
  --line:#d9d9d9;
}
*{margin:0;padding:0;box-sizing:border-box}
html,body{width:1200px;height:3243px;overflow:hidden;background:var(--white)}
body{position:relative;font-family:'Roboto',Arial,sans-serif;color:var(--text)}
.abs{position:absolute}
.site-header{left:0;top:0;width:1200px;height:84px;background:var(--white)}
.brand{left:112px;top:10px;display:flex;align-items:center;gap:12px}
.brand-mark{width:46px;height:46px;border-radius:50%;background:var(--purple)}
.brand-name{font-size:46px;font-weight:500;color:var(--purple);letter-spacing:1px;line-height:1}
.main-nav{top:33px;font-size:15px;color:var(--ink)}
.nav-icons{left:968px;top:26px;display:flex;gap:16px}
.hero{left:0;top:84px;width:1200px;height:544px;background:linear-gradient(90deg,#5a4438 0%,#3c3533 40%,#4a4a4c 55%,#2e2e30 100%)}
.hero-title{left:0;top:228px;width:1200px;text-align:center;color:var(--white);font-size:78px;font-weight:700;letter-spacing:0.5px}
.hero-sub{left:0;top:332px;width:1200px;text-align:center;color:var(--white);font-size:30px;font-weight:400}
.hero-btn{left:530px;top:409px;width:140px;height:40px;border:2px solid var(--white);color:var(--white);font-size:15px;display:flex;align-items:center;justify-content:center}
.section-title{color:var(--purple);font-weight:700}
.products-title{left:0;top:708px;width:1200px;text-align:center;font-size:38px}
.products-intro{left:0;top:779px;width:1200px;text-align:center;font-size:16px;color:var(--ink)}
.product-photo{top:849px;width:317px;height:311px}
.product-name{top:1178px;font-size:21px;font-weight:500;color:var(--ink)}
.product-price{top:1211px;font-size:21px;color:var(--purple)}
.gallery-title{left:111px;top:1309px;font-size:42px}
.video{left:112px;top:2198px;width:977px;height:509px;background:linear-gradient(110deg,#2a2326 0%,#3a2c34 45%,#2c2030 75%,#3b2a45 100%)}
.play{left:559px;top:2393px;width:82px;height:82px;border-radius:50%;background:var(--white);display:flex;align-items:center;justify-content:center}
.rule{left:0;width:1200px;height:1px;background:var(--line)}
.foot-head{top:2840px;font-size:21px;font-weight:500;color:var(--ink)}
.foot-list{top:2882px;font-size:15.5px;line-height:22px;color:var(--ink);list-style:none}
.newsletter-title{left:112px;top:3036px;font-size:21px;font-weight:500;color:var(--ink)}
.newsletter{left:112px;top:3088px;width:284px;height:48px;border:1px solid #333;display:flex;align-items:center;justify-content:space-between;padding:0 12px 0 9px;font-size:9px;color:#333}
.social{left:980px;top:3041px;display:flex;gap:18px}
.social span{width:24px;height:24px;background:var(--ink);border-radius:3px}
.copyright{left:111px;top:3208px;font-size:16px;color:var(--ink)}
</style>
</head>
<body>
<header class="site-header abs">
  <div class="brand abs"><span class="brand-mark"></span><span class="brand-name">Kelmo</span></div>
  <span class="main-nav abs" style="left:541px">Home</span>
  <span class="main-nav abs" style="left:610px">About Us</span>
  <span class="main-nav abs" style="left:700px">Products</span>
  <span class="main-nav abs" style="left:788px">Contact Us</span>
  <div class="nav-icons abs">
    <svg width="32" height="32" viewBox="0 0 32 32"><circle cx="12" cy="12" r="9" fill="none" stroke="#111" stroke-width="3"/><line x1="19" y1="19" x2="30" y2="30" stroke="#111" stroke-width="4" stroke-linecap="round"/></svg>
    <svg width="30" height="32" viewBox="0 0 30 32"><circle cx="15" cy="9" r="8" fill="#111"/><path d="M1 32 Q1 18 15 18 Q29 18 29 32 Z" fill="#111"/></svg>
    <svg width="28" height="32" viewBox="0 0 28 32"><path d="M8 11 V7 a6 6 0 0 1 12 0 V11" fill="none" stroke="#111" stroke-width="3"/><rect x="2" y="10" width="24" height="22" rx="3" fill="#111"/></svg>
  </div>
</header>

<section class="hero abs" role="img" aria-label="Man scooping supplement powder beside dumbbells and supplement tubs in a dim gym"></section>
<h1 class="hero-title abs">WELCOME TO&nbsp; KELMO</h1>
<p class="hero-sub abs">FUELING HEALTH,NOT EXPENSES</p>
<div class="hero-btn abs">Contact Us</div>

<h2 class="section-title products-title abs">Our Products</h2>
<p class="products-intro abs">Excepteur sint occaecat cupidatat non proident, sunt in culpa qui officia deserunt mollit anim id est laborum.</p>

<div class="product-photo abs" style="left:112px;background:linear-gradient(160deg,#b9c3c9,#d7cfc7 60%,#e6e3df)" role="img" aria-label="Woman stretching her arms in a fitness class"></div>
<div class="product-photo abs" style="left:442px;background:linear-gradient(150deg,#2c2e31,#45484b 55%,#2a2b2d)" role="img" aria-label="Scoop of creatine powder over a shaker with capsules on a dark table"></div>
<div class="product-photo abs" style="left:771px;background:linear-gradient(160deg,#6c6f72,#a7a4a0 50%,#3a3a3c)" role="img" aria-label="Man with a towel drinking a protein shake in a gym"></div>
<span class="product-name abs" style="left:112px">Pre-Workout</span>
<span class="product-name abs" style="left:442px">Creatine</span>
<span class="product-name abs" style="left:771px">Protein Shakes</span>
<span class="product-price abs" style="left:113px">$ 500.00</span>
<span class="product-price abs" style="left:443px">$ 700.00</span>
<span class="product-price abs" style="left:772px">$ 600.00</span>

<h2 class="section-title gallery-title abs">Gallery</h2>
<div class="abs" style="left:112px;top:1400px;width:641px;height:713px;background:linear-gradient(135deg,#e9e8e5,#dcd8d2 55%,#cbbfb4)" role="img" aria-label="Man in a white t-shirt drinking from a black shaker next to a supplement tub"></div>
<div class="abs" style="left:762px;top:1400px;width:327px;height:320px;background:linear-gradient(140deg,#3a3a3a,#5d5c5a 50%,#2b2b2b)" role="img" aria-label="Bowl of white powder with capsules and a dumbbell on dark stone"></div>
<div class="abs" style="left:762px;top:1793px;width:327px;height:320px;background:linear-gradient(150deg,#4a4c55,#8d8a8c 50%,#2f2f33)" role="img" aria-label="Two women stretching on the floor of a gym"></div>

<div class="video abs" role="img" aria-label="Video still of a man resting on the gym floor after a workout"></div>
<div class="play abs"><svg width="30" height="32" viewBox="0 0 30 32"><path d="M5 2 L28 16 L5 30 Z" fill="var(--purple)"/></svg></div>

<div class="rule abs" style="top:2791px"></div>
<h3 class="foot-head abs" style="left:112px">Quick links</h3>
<h3 class="foot-head abs" style="left:473px">Contact Us</h3>
<h3 class="foot-head abs" style="left:837px">About Us</h3>
<ul class="foot-list abs" style="left:112px"><li>Home</li><li>About Us</li><li>Products</li><li>Contact Us</li></ul>
<ul class="foot-list abs" style="left:476px;width:190px"><li>no 2417 Kelmo, Harbor Lane, Westbrook 61204.</li><li>+ 1 555-014-2290</li><li>info@kelmo-shop.com</li></ul>
<p class="foot-list abs" style="left:840px;width:252px">Lorem ipsum dolor sit amet, consectetur adipiscing elit, sed do eiusmod tempor incididunt ut labore et dolore magna aliqua.</p>

<h3 class="newsletter-title abs">Lorem Ipsum</h3>
<div class="newsletter abs"><span>Email Address</span><svg width="26" height="12" viewBox="0 0 26 12"><path d="M1 6 H24 M19 1 L24 6 L19 11" fill="none" stroke="#111" stroke-width="2"/></svg></div>
<div class="social abs"><span></span><span></span><span></span></div>

<div class="rule abs" style="top:3187px"></div>
<p class="copyright abs">Copyright © 2023 Kelmo. All rights reserved.</p>
</body>
</html>
```